RW Framewell Inc Business cards

We need business cards using our existing logo but slightly modified. Right now the logo says RW Loadbearing Masonry. We want to keep the RW part of the design, but replace the Structural Concrete portion with "FRAMEWELL". Please see the attached file.
Ideally this would be a blank template so we can add Different Names, titles, and phone numbers later.
On the one side we want only the logo and on the other side the detail. I'm attaching an example for you to see.
Please reach out with any other questions. Our address and other details will be given out once we find a design we like.

Target Market(s)

Construction Industry

```html
<!DOCTYPE html>
<html lang="en">
<head>
<meta charset="utf-8">
<title>RW Framewell Inc – Business Cards</title>
<link rel="stylesheet" href="https://fonts.googleapis.com/css2?family=Bebas+Neue&family=Arimo:wght@400;700&family=Questrial&display=swap">
<style>
  :root {
    --page-bg: #ecebe8;
    --card-white: #ffffff;
    --brand-blue: #1570b8;
    --back-blue: #3d87bb;
    --logo-cream: #dcd98f;
    --faint-blue: #cfe2f1;
    --text-grey: #4a4a4a;
    --title-grey: #8a8a8a;
  }
  * { box-sizing: border-box; margin: 0; padding: 0; }
  html, body {
    width: 1125px;
    height: 1200px;
    overflow: hidden;
    background: var(--page-bg);
  }
  .card {
    position: absolute;
    left: 162px;
    width: 800px;
    height: 456px;
    box-shadow: 0 2px 6px rgba(0,0,0,0.18);
    overflow: hidden;
  }
  .card--front { top: 100px; background: var(--card-white); }
  .card--back  { top: 620px; background: var(--back-blue); }

  .accent-bar {
    position: absolute;
    left: 0; top: 68px;
    width: 10px; height: 60px;
    background: var(--brand-blue);
  }
  .person-name {
    position: absolute;
    left: 60px; top: 64px;
    font-family: "Bebas Neue", "Oswald", sans-serif;
    font-size: 44px;
    letter-spacing: 0.5px;
    color: var(--brand-blue);
    line-height: 1;
  }
  .person-title {
    position: absolute;
    left: 61px; top: 112px;
    font-family: "Arimo", Arial, sans-serif;
    font-weight: 700;
    font-size: 18px;
    color: var(--title-grey);
  }
  .contact-list {
    position: absolute;
    left: 60px; top: 160px;
    list-style: none;
    font-family: "Arimo", Arial, sans-serif;
    font-size: 18px;
    color: var(--text-grey);
  }
  .contact-list li {
    display: flex;
    align-items: center;
    height: 26px;
  }
  .contact-list svg {
    width: 14px; height: 14px;
    margin-right: 11px;
    fill: var(--brand-blue);
    flex: none;
  }
  .social-row {
    position: absolute;
    left: 61px; top: 372px;
    display: flex;
    gap: 3px;
  }
  .social-dot {
    width: 33px; height: 33px;
    border-radius: 50%;
    background: var(--brand-blue);
  }
  .faint-panel {
    position: absolute;
    right: 16px; top: 0;
    width: 172px; height: 456px;
    background: var(--faint-blue);
    opacity: 0.75;
  }

  .brand-lockup {
    position: absolute;
    inset: 0;
    display: flex;
    flex-direction: column;
    align-items: center;
    justify-content: center;
    font-family: "Questrial", "Arimo", sans-serif;
    font-weight: 400;
    color: var(--logo-cream);
    padding-top: 20px;
  }
  .brand-lockup__mark {
    font-size: 150px;
    line-height: 1;
    letter-spacing: 6px;
  }
  .brand-lockup__word {
    font-size: 44px;
    letter-spacing: 7px;
    margin-top: 6px;
  }
</style>
</head>
<body>
  <section class="card card--front" aria-label="Card front with contact details">
    <div class="accent-bar"></div>
    <h1 class="person-name">Daniel Hartley</h1>
    <p class="person-title">President</p>
    <ul class="contact-list">
      <li>
        <svg viewBox="0 0 16 16" aria-hidden="true"><path d="M3.6 1.2l2.3 2.6c.4.4.3 1-.1 1.4L4.7 6.4c.9 2 2.6 3.8 4.8 4.8l1.2-1.2c.4-.4 1-.4 1.4-.1l2.6 2.3c.4.4.4 1 0 1.4l-1.2 1.2C11.6 16.7 0 6.6 1.3 2.4L2.2 1.2c.4-.4 1-.4 1.4 0z"/></svg>
        <span>555-214-7630</span>
      </li>
      <li>
        <svg viewBox="0 0 16 16" aria-hidden="true"><path d="M4.5 0h7c.8 0 1.5.7 1.5 1.5v13c0 .8-.7 1.5-1.5 1.5h-7C3.7 16 3 15.3 3 14.5v-13C3 .7 3.7 0 4.5 0zm.3 2v10.5h6.4V2H4.8zM8 13.3a.9.9 0 100 1.8.9.9 0 000-1.8z"/></svg>
        <span>555-318-4096</span>
      </li>
      <li>
        <svg viewBox="0 0 16 16" aria-hidden="true"><path d="M1 3h14v1.2L8 8.6 1 4.2V3zm0 2.6l7 4.4 7-4.4V13H1V5.6z"/></svg>
        <span>info@rwframewell.com</span>
      </li>
      <li>
        <svg viewBox="0 0 16 16" aria-hidden="true"><circle cx="8" cy="8" r="7"/><path d="M4 5c1.5-.5 2.5.5 2.5 1.5S5 8 5.5 9.5 7 11 7 13M11 3.5c-1 1-.5 2.5.5 3s2 .5 2.5 2" stroke="#fff" stroke-width="1.2" fill="none"/></svg>
        <span>www.rwframewell.com</span>
      </li>
    </ul>
    <div class="social-row" aria-label="Social media links">
      <span class="social-dot"></span>
      <span class="social-dot"></span>
      <span class="social-dot"></span>
    </div>
    <div class="faint-panel" role="img" aria-label="Large faint brand mark decoration"></div>
  </section>

  <section class="card card--back" aria-label="Card back with company name">
    <div class="brand-lockup">
      <span class="brand-lockup__mark">RW</span>
      <span class="brand-lockup__word">Framewell</span>
    </div>
  </section>
</body>
</html>
```